New Fitness Company looking for creative website design

I am building a new fitness matching service. To match customers looking for fitness services to professionals that meet their requirements

My business will have 5 different divisions and I would like to have tabs for each division

1. Matching client to trainer - I need to have video upload capability on the site
2. Corporate personal training services

-The site needs a shopping cart as well as payment capability.
- I am looking for the site to be bright and inviting as well as have clients and trainers going through some type of workout on the main page.
- I also need the capability to capture email addresses
- We are going to have a section that ask the customer questions to match up the trainer so that needs to be a part of the site
-Ability to have trainers rated in a 1 star to 5 stars as well as reviews
- Site should be inviting, bright and vibrant colors that catch the eye and is easy to use
- Similar sites for inspiration are www.zavrello.com where you give a description of how the service works, short video and various services.

Target Market(s)

mid income to high income, mix of female and male customers

Industry/Entity Type

Fitness

Coding

Coded - Design and coding required

Number of Pages Required

5+ page

Font styles to use
Serif
Sans Serif

Requirements
Must have
• Must have the logos that I provided in the website
Should not have
• Not looking for bodybuilders on website. This is for everyday people that are interested in staying in shape and working out. So active fit people will resonate with my prospects

```html
<!DOCTYPE html>
<html lang="en">
<head>
<meta charset="utf-8">
<title>Vantrel Fitness</title>
<link href="https://fonts.googleapis.com/css2?family=Open+Sans:wght@400;600;700&family=Quicksand:wght@400;500;600&display=swap" rel="stylesheet">
<style>
:root{
  --green:#3cb54a;
  --green-dark:#2e9b3b;
  --green-band:#2f9a3c;
  --orange:#f39320;
  --orange-dark:#e07e10;
  --ink:#333;
  --muted:#888;
  --line:#e3e3e3;
  --topbar:#1f2a22;
  --footer:#1c1c1c;
  --white:#fff;
}
*{box-sizing:border-box;margin:0;padding:0}
html,body{width:1200px;height:3191px;overflow:hidden;background:var(--white)}
body{position:relative;font-family:"Open Sans",Arial,sans-serif;color:var(--ink)}
.abs{position:absolute}
.heading{font-family:"Quicksand",Arial,sans-serif;font-weight:500}
.center{text-align:center}

/* top bar */
.topbar{left:0;top:0;width:1200px;height:30px;background:var(--topbar);color:#fff;font-size:11px;font-weight:600;letter-spacing:.3px}
.topbar span{position:absolute;top:8px;display:flex;align-items:center;gap:6px}
.topbar i{display:inline-block;width:9px;height:9px;border-radius:50%;background:#fff}

/* header */
.follow{left:98px;top:104px;font-size:11px;font-weight:700;color:var(--orange);display:flex;align-items:center;gap:6px}
.social{width:24px;height:24px;border-radius:50%;display:inline-block}
.brand{left:450px;top:60px;width:300px;text-align:center}
.brand-mark{width:54px;height:54px;border-radius:50%;background:var(--green);margin:0 auto 8px}
.brand-name{font-family:"Open Sans",sans-serif;font-weight:700;font-size:26px;color:var(--green);letter-spacing:2px}
.search{left:860px;top:98px;width:240px;height:34px;border:1px solid var(--line);display:flex}
.search span{flex:1;font-size:10px;color:#aaa;padding:10px 12px}
.search b{width:36px;background:var(--orange);display:flex;align-items:center;justify-content:center}

/* nav */
.nav{left:0;top:196px;width:1200px;height:55px;background:var(--green)}
.nav a{position:absolute;top:20px;transform:translateX(-50%);color:#fff;font-size:11px;font-weight:700;text-decoration:none;letter-spacing:.3px}
.nav .active{left:98px;top:4px;width:123px;height:47px;background:#fff;border-bottom:3px solid var(--orange)}
.nav .active a{color:var(--orange);left:61px;top:25px}
.nav .active em{position:absolute;left:50px;top:6px;width:22px;height:16px;border-radius:50%;background:#f6c98e}

/* hero */
.hero{left:0;top:251px;width:1200px;height:558px;background:linear-gradient(180deg,#f7f7f5 0%,#eeeeea 70%,#d9c29c 71%,#e6d1ad 100%)}
.hero-figure{left:410px;top:15px;width:720px;height:510px;background:radial-gradient(ellipse at 45% 55%,#e9c7ac 0%,#f2e4d8 45%,rgba(240,240,236,0) 72%)}
.hero-box{left:98px;top:430px;width:387px;height:196px;background:rgba(255,255,255,.95);border-bottom:4px solid var(--orange);padding:22px 22px}
.hero-box h1{font-size:36px;color:#333;font-weight:500}
.hero-box p{margin-top:10px;font-size:12.5px;font-weight:700;color:var(--orange);line-height:22px}
.btn{display:inline-block;background:var(--orange);color:#fff;font-size:13px;padding:10px 20px;margin-top:12px;border-radius:2px}
.dots{left:98px;top:666px;display:flex;gap:6px}
.dots i{width:13px;height:13px;border-radius:50%;background:#fff;border:1px solid #ccc}
.dots i.on{background:var(--green);border-color:var(--green)}

/* section titles */
.title{font-family:"Quicksand",sans-serif;font-weight:500;font-size:28px;color:var(--green);width:1200px;left:0;text-align:center}
.lead{left:210px;width:780px;font-size:12.5px;color:#888;line-height:24px;text-align:center}

/* video */
.video{left:181px;top:990px;width:802px;height:440px;background:#000}
.video-scene{position:absolute;left:0;top:0;width:802px;height:410px;background:linear-gradient(90deg,#c77d62 0%,#e2a38c 35%,#f1d2c3 55%,#d69a7f 80%,#b96e5b 100%)}
.play{position:absolute;left:365px;top:176px;width:74px;height:52px;background:rgba(30,30,30,.85);border-radius:6px}
.play svg{position:absolute;left:27px;top:14px}
.controls{position:absolute;left:0;top:410px;width:802px;height:30px;background:#1b1b1b;color:#ccc;font-size:10px}
.controls .bar{position:absolute;left:0;top:0;width:802px;height:4px;background:#444}
.controls .bar b{display:block;width:160px;height:4px;background:#d33}

/* services */
.divider{left:98px;top:1581px;width:1004px;height:1px;background:var(--line)}
.svc-icon{width:106px;height:106px;border-radius:50%;top:1709px;display:flex;align-items:center;justify-content:center}
.svc{top:1832px;width:300px;text-align:center}
.svc h3{font-size:14px;font-weight:400;color:#333;margin-bottom:8px}
.svc p{font-size:11px;color:#888;line-height:21px}
.vline{width:1px;height:190px;top:1734px;background:var(--line)}

/* corporate band */
.band{left:0;top:1992px;width:1200px;height:387px;background:linear-gradient(180deg,rgba(47,154,60,.92),rgba(40,140,52,.95)),linear-gradient(90deg,#6a8f5e,#9bb98a,#6a8f5e)}
.band .title{color:#fff}
.card{top:2117px;width:483px;height:192px;background:#fff;display:flex}
.card-img{width:213px;height:192px}
.card-body{padding:14px 18px;flex:1}
.card-body h4{font-size:14px;font-weight:400;color:#333}
.card-body p{font-size:11px;color:#888;line-height:19px;margin-top:8px}
.card-body .more{color:var(--orange);font-size:11px;display:block;margin-top:8px}
.card-body .share{border-top:1px solid var(--line);margin-top:10px;padding-top:10px;display:flex;gap:14px}
.card-body .share i{width:8px;height:8px;background:#aaa;border-radius:50%}
.arrow{top:2180px}

/* faq / rating / newsletter */
.col-title{top:2446px;font-size:17px;color:#333}
.col-nav{top:2450px;color:#aaa;font-size:12px;letter-spacing:6px}
.faq-item{left:98px;width:302px;display:flex;gap:14px}
.faq-q{width:50px;height:50px;border-radius:50%;background:var(--orange);color:#fff;font-weight:700;font-size:20px;display:flex;align-items:center;justify-content:center;flex:none}
.faq-item h5{font-size:12.5px;font-weight:400;color:#333;margin-top:4px}
.faq-item p{font-size:11px;color:#888;line-height:18px;margin-top:3px}
.hr{height:1px;background:var(--line)}
.rating{left:447px;top:2494px;width:304px;height:230px;background:#f1f1f1;border-bottom:3px solid #ddd;padding:22px 24px}
.rating p{font-size:11px;font-style:italic;color:#555;line-height:21px;padding-left:16px}
.rating .quote{position:absolute;font-size:34px;color:#bbb;font-family:Georgia,serif}
.rating .who{display:flex;align-items:center;gap:10px;margin-top:12px}
.avatar{width:42px;height:42px;border-radius:50%;background:linear-gradient(#b98a6f,#7a553f)}
.who span{font-size:11px;color:var(--orange);font-weight:600}
.newsletter{left:798px;top:2494px;width:302px;height:230px;border:1px solid var(--line);padding:22px 14px}
.field{border:1px solid #ddd;height:33px;font-size:10px;color:#777;padding:10px 8px;margin-bottom:10px}
.field.tall{height:64px}
.newsletter .btn{margin-top:0;font-size:12px;padding:9px 26px}

/* products */
.products{left:0;top:2788px;width:1200px;height:304px;background:linear-gradient(90deg,#2a3326,#3f4a35 35%,#2c3328 65%,#1f251d)}
.products .title{color:#fff;top:2830px}
.prod{top:2894px;width:166px;height:143px;border:3px solid #fff}
.sale{position:absolute;right:8px;top:6px;width:44px;height:44px;border-radius:50%;background:var(--orange);color:#fff;font-size:11px;display:flex;align-items:center;justify-content:center}
.cart-btn{position:absolute;left:30px;top:54px;border:1px solid #fff;color:#fff;font-size:11px;padding:8px 10px}

/* footer */
.footer{left:0;top:3092px;width:1200px;height:99px;background:var(--footer);color:#ccc}
.footer a{position:absolute;top:30px;transform:translateX(-50%);font-size:11px;color:#ccc;text-decoration:none}
.footer a::before{content:"• "}
.copy{position:absolute;left:0;width:1200px;top:70px;text-align:center;font-size:10px;color:#999}
</style>
</head>
<body>

<!-- top bar -->
<div class="abs topbar">
  <span style="left:117px"><i></i>LOGIN</span>
  <span style="left:191px"><i></i>SIGN UP</span>
  <span style="left:808px"><i></i>CALL US: 123-123-1234</span>
  <span style="left:953px"><i></i>SHOP YOUR PRODUCTS</span>
</div>

<!-- header -->
<div class="abs follow">FOLLOW WITH US :
  <span class="social" style="background:#3b5998"></span>
  <span class="social" style="background:#4fa9e5"></span>
  <span class="social" style="background:#555"></span>
  <span class="social" style="background:#1d6fa3"></span>
</div>
<div class="abs brand">
  <div class="brand-mark"></div>
  <div class="brand-name">VANTREL FITNESS</div>
</div>
<div class="abs search"><span>SEARCH</span><b><svg width="12" height="12" viewBox="0 0 12 12"><circle cx="5" cy="5" r="3.5" stroke="#fff" stroke-width="1.6" fill="none"/><line x1="7.5" y1="7.5" x2="11" y2="11" stroke="#fff" stroke-width="1.6"/></svg></b></div>

<!-- nav -->
<nav class="abs nav">
  <div class="abs active"><em></em><a href="#">HOME</a></div>
  <a href="#" style="left:291px">ABOUT US</a>
  <a href="#" style="left:419px">STORE</a>
  <a href="#" style="left:540px">VIDEOS</a>
  <a href="#" style="left:672px">PRODUCTS</a>
  <a href="#" style="left:811px">TRAINING</a>
  <a href="#" style="left:932px">FAQ</a>
  <a href="#" style="left:1064px">CONTACT US</a>
</nav>

<!-- hero -->
<section class="abs hero">
  <div class="abs hero-figure" role="img" aria-label="Woman in white activewear stretching on a wooden floor"></div>
</section>
<div class="abs hero-box">
  <h1 class="heading">Need a Fitness Body..!</h1>
  <p>SED UT PERSPICIATIS UNDE OMNIS ISTE NATUS ERROR SIT APERIAM, EAQUE IPSA QUAE AB ILLO INVE...</p>
  <span class="btn">Shop Now!</span>
</div>
<div class="abs dots"><i class="on"></i><i></i><i></i></div>

<!-- matching -->
<h2 class="abs title" style="top:862px">Matching Client to Trainer</h2>
<p class="abs lead" style="top:907px">Nemo enim ipsam voluptatem quia voluptas sit aspernatur aut odit aut fugit, sed quia consequuntur magni dolores eos qui ratione voluptatem sequi nesciunt. Neque porro quisquam est, qui dolorem ipsum quia...</p>

<div class="abs video">
  <div class="video-scene" role="img" aria-label="Two women chatting and eating yogurt after a workout"></div>
  <div class="play"><svg width="22" height="24" viewBox="0 0 22 24"><polygon points="0,0 22,12 0,24" fill="#fff"/></svg></div>
  <div class="controls"><div class="bar"><b></b></div>
    <svg class="abs" style="left:16px;top:13px" width="10" height="10"><rect x="0" y="0" width="3" height="10" fill="#ccc"/><rect x="6" y="0" width="3" height="10" fill="#ccc"/></svg>
    <span class="abs" style="left:90px;top:12px">0:06 / 0:24</span>
    <span class="abs" style="left:700px;top:12px">360p</span>
  </div>
</div>
<p class="abs lead" style="left:120px;width:960px;top:1458px;font-size:11px;line-height:23px">Accusantium doloremque laudantium, totam rem aperiam, eaque ipsa quae ab veritatis et quasi architecto beatae vitae dicta sunt explicabo. Nemo enim ipsam voluptatem quia voluptas sit aspernatur aut odit aut fugit, sed quia consequuntur magni dolores eos qui ratione voluptatem sequi nesciunt.<br>Neque porro quisquam est...</p>

<div class="abs divider"></div>

<!-- services -->
<h2 class="abs title" style="top:1630px">Our Services</h2>
<div class="abs svc-icon" style="left:187px;background:var(--orange)"><svg width="40" height="40" viewBox="0 0 40 40" fill="none" stroke="#fff" stroke-width="2.5"><circle cx="20" cy="8" r="4"/><path d="M8 14l12 4 12-4M20 18v10l-6 9M20 28l6 9"/></svg></div>
<div class="abs svc-icon" style="left:547px;background:var(--green)"><svg width="40" height="40" viewBox="0 0 40 40" fill="none" stroke="#fff" stroke-width="2.5"><path d="M8 32C8 14 22 8 34 8c0 14-8 24-26 24zM8 32l16-16"/></svg></div>
<div class="abs svc-icon" style="left:907px;background:#2b2b2b"><svg width="44" height="40" viewBox="0 0 44 40" fill="none" stroke="#fff" stroke-width="2.5"><circle cx="22" cy="13" r="6"/><circle cx="9" cy="16" r="4"/><circle cx="35" cy="16" r="4"/><path d="M10 34c0-8 6-12 12-12s12 4 12 12M2 32c0-6 3-9 7-9M42 32c0-6-3-9-7-9"/></svg></div>
<div class="abs vline" style="left:421px"></div>
<div class="abs vline" style="left:781px"></div>
<div class="abs svc" style="left:90px"><h3>Similique sunt in culpa</h3><p>Nemo enim ipsam voluptatem quia voluptas sit tur aut odit aut fugit, sed quia consequuntur magni dolores eos qui ratione voluptatem sequi nesci...</p></div>
<div class="abs svc" style="left:450px"><h3>Similique sunt in culpa</h3><p>Nemo enim ipsam voluptatem quia voluptas sit tur aut odit aut fugit, sed quia consequuntur magni dolores eos qui ratione voluptatem sequi nesci...</p></div>
<div class="abs svc" style="left:810px"><h3>Similique sunt in culpa</h3><p>Nemo enim ipsam voluptatem quia voluptas sit tur aut odit aut fugit, sed quia consequuntur magni dolores eos qui ratione voluptatem sequi nesci...</p></div>

<!-- corporate -->
<section class="abs band" role="img" aria-label="Group fitness class in a gym under a green overlay"></section>
<h2 class="abs title" style="top:2046px;color:#fff">Corporate Personal Training</h2>
<svg class="abs arrow" style="left:52px" width="22" height="70" viewBox="0 0 22 70"><polyline points="20,2 2,35 20,68" fill="none" stroke="#fff" stroke-width="1.5"/></svg>
<svg class="abs arrow" style="left:1128px" width="22" height="70" viewBox="0 0 22 70"><polyline points="2,2 20,35 2,68" fill="none" stroke="#fff" stroke-width="1.5"/></svg>
<div class="abs card" style="left:100px">
  <div class="card-img" role="img" aria-label="Two people doing floor exercises on an orange backdrop" style="background:linear-gradient(135deg,#e8752a,#c9541c)"></div>
  <div class="card-body"><h4>Nemo enim ipsam voluptatem</h4><p>Consequuntur magni dolores eos sequi nesc sunt. Neque porro quisquamlorem ipsum qu ia dolor sit amet, eius...</p><span class="more">Read More»</span><div class="share"><i></i><i></i><i></i><i></i><i></i><i></i></div></div>
</div>
<div class="abs card" style="left:619px">
  <div class="card-img" role="img" aria-label="Senior couple stretching outdoors on grass" style="background:linear-gradient(180deg,#b9d6e8,#8fbf6a)"></div>
  <div class="card-body"><h4>Nemo enim ipsam voluptatem</h4><p>Consequuntur magni dolores eos sequi nesc sunt. Neque porro quisquamlorem ipsum qu ia dolor sit amet, eius...</p><span class="more">Read More»</span><div class="share"><i></i><i></i><i></i><i></i><i></i><i></i></div></div>
</div>

<!-- faq -->
<h3 class="abs col-title heading" style="left:98px">FAQ</h3>
<span class="abs col-nav" style="left:378px">‹›</span>
<div class="abs faq-item" style="top:2505px"><div class="faq-q">?</div><div><h5>Porro quisquam est, qui dolorem ips</h5><p>Encounter consequences that are painful. Nor again is there anyone who loves...</p></div></div>
<div class="abs hr" style="left:98px;top:2573px;width:302px"></div>
<div class="abs faq-item" style="top:2588px"><div class="faq-q">?</div><div><h5>Porro quisquam est, qui dolorem ips</h5><p>Encounter consequences that are painful. Nor again is there anyone who loves...</p></div></div>
<div class="abs hr" style="left:98px;top:2656px;width:302px"></div>
<div class="abs faq-item" style="top:2672px"><div class="faq-q">?</div><div><h5>Porro quisquam est, qui dolorem ips</h5><p>Encounter consequences that are painful. Nor again is there anyone who loves...</p></div></div>

<!-- rating -->
<h3 class="abs col-title heading" style="left:447px">Trainer Rating</h3>
<span class="abs col-nav" style="left:730px">‹›</span>
<div class="abs rating">
  <span class="quote" style="left:14px;top:8px">“</span>
  <p>Similique sunt in culpa qui officia deserunt quidem rerum facilis est et expedita distinctio. Nam libero tempore, cum soluta nobis est eligendi optio cumque nihil impedit quo minus id quod maxime placeat facere possimus, omnis voluptas</p>
  <span class="quote" style="right:16px;top:150px">”</span>
  <div class="who"><div class="avatar" role="img" aria-label="Trainer reviewer portrait"></div><span>-John Doe</span>
    <svg width="60" height="11" viewBox="0 0 60 11"><g fill="#f3b21b"><polygon points="5.5,0 7,4 11,4 8,6.5 9,10.5 5.5,8 2,10.5 3,6.5 0,4 4,4"/><polygon transform="translate(12)" points="5.5,0 7,4 11,4 8,6.5 9,10.5 5.5,8 2,10.5 3,6.5 0,4 4,4"/><polygon transform="translate(24)" points="5.5,0 7,4 11,4 8,6.5 9,10.5 5.5,8 2,10.5 3,6.5 0,4 4,4"/><polygon transform="translate(36)" points="5.5,0 7,4 11,4 8,6.5 9,10.5 5.5,8 2,10.5 3,6.5 0,4 4,4"/></g><polygon transform="translate(48)" fill="#ccc" points="5.5,0 7,4 11,4 8,6.5 9,10.5 5.5,8 2,10.5 3,6.5 0,4 4,4"/></svg>
  </div>
</div>

<!-- newsletter -->
<h3 class="abs col-title heading" style="left:798px">Newsletter</h3>
<form class="abs newsletter">
  <div class="field">Enter Your Name*</div>
  <div class="field">Enter Your E-mail*</div>
  <div class="field tall">Type Your Message*</div>
  <span class="btn">Sign Up</span>
</form>

<!-- products -->
<section class="abs products" role="img" aria-label="Smiling people working out, darkened background"></section>
<h2 class="abs title" style="top:2830px;color:#fff">Our Products</h2>
<svg class="abs" style="left:100px;top:2930px" width="18" height="70" viewBox="0 0 18 70"><polyline points="16,2 2,35 16,68" fill="none" stroke="#fff" stroke-width="1.5"/></svg>
<svg class="abs" style="left:1078px;top:2930px" width="18" height="70" viewBox="0 0 18 70"><polyline points="2,2 16,35 2,68" fill="none" stroke="#fff" stroke-width="1.5"/></svg>
<div class="abs prod" style="left:234px;background:var(--green)"><div class="sale" style="background:rgba(255,255,255,.25)">Sale</div><span class="cart-btn">🛒 Add to Cart</span></div>
<div class="abs prod" role="img" aria-label="Protein powder in a bowl" style="left:423px;background:linear-gradient(#efe6da,#b68a5e)"><div class="sale">Sale</div></div>
<div class="abs prod" role="img" aria-label="Oatmeal bowl with berries" style="left:611px;background:linear-gradient(#f4f0ea,#d9584f)"><div class="sale">Sale</div></div>
<div class="abs prod" role="img" aria-label="Supplement containers and shaker" style="left:800px;background:linear-gradient(#d9d9d9,#3a3a3a)"><div class="sale">Sale</div></div>

<!-- footer -->
<footer class="abs footer">
  <a href="#" style="left:130px">HOME</a>
  <a href="#" style="left:262px">ABOUT US</a>
  <a href="#" style="left:390px">STORE</a>
  <a href="#" style="left:512px">VIDEOS</a>
  <a href="#" style="left:648px">PRODUCTS</a>
  <a href="#" style="left:785px">TRAINING</a>
  <a href="#" style="left:908px">FAQ</a>
  <a href="#" style="left:1036px">CONTACT US</a>
  <div class="copy">COPYRIGHTS © VANTREL 2015 | ALLRIGHTS RESERVED.</div>
</footer>

</body>
</html>
```